Flat bootstrap design for existing site

I'm looking for a modern flat design based around an existing logo. This has to be a custom design (no external templates), and implemented into a bootstrap framework.

The logo is attached as 2 versions - choose whichever you want, that flows better with whatever design you choose.

Added screenshots of the existing site (currently using the default bootstrap layouts). Please make your designs around those pages in the screenshots (i.e. the homepage only has the postal code input and the header). The active page has 3 screenshots, because I wanted to illustrate the other states that would be visible (in the table rows).

This is a moving/junk removal website, just for some context.

Here's some example websites (flat designs) that I like, just to give you an idea of what I'm after.

https://www.plimvora.com/
https://dacklow.com/
https://trevanu.com/
https://quobrintal.com/en/

Coding

Coded - Design and coding required

Number of Pages Required

5+ page

Colors

Designer to choose colors to be used in the design.

Requirements
Must have
• It must be a modern/simple flat design, that is built around the existing logo (attached).
• It has to be implemented using bootstrap.

```html
<!DOCTYPE html>
<html lang="en">
<head>
<meta charset="utf-8">
<title>Yakhaul – Sign in</title>
<link href="https://fonts.googleapis.com/css2?family=Raleway:wght@400;500;600;700&display=swap" rel="stylesheet">
<style>
  :root {
    --sky: #4ac8f5;
    --white: #ffffff;
    --ink: #666666;
    --muted: #8a8a8a;
    --rule: #d4d4d4;
    --field-border: #b9b9b9;
    --nav-pill: #707070;
    --footer: #050505;
    --worker-a: #f0a43a;
    --worker-b: #e98a33;
    --soc-1: #3b5b98;
    --soc-2: #55acee;
    --soc-3: #e8322b;
    --soc-4: #cd201f;
    --soc-5: #a33ab2;
  }
  * { box-sizing: border-box; margin: 0; padding: 0; }
  html, body { width: 1200px; height: 675px; overflow: hidden; }
  body {
    position: relative;
    font-family: "Raleway", sans-serif;
    background: var(--sky);
    color: var(--white);
  }
  .site-header {
    position: absolute; left: 0; top: 0; width: 1200px; height: 90px;
  }
  .brand {
    position: absolute; left: 86px; top: 30px;
    font-size: 34px; font-weight: 700; letter-spacing: 1px; color: var(--white);
    display: flex; align-items: center; gap: 10px;
  }
  .brand-dot { width: 18px; height: 18px; border-radius: 50%; background: var(--white); }
  .main-nav {
    position: absolute; top: 35px; right: 86px;
    display: flex; align-items: center; gap: 40px;
    font-size: 15px; font-weight: 500; text-transform: uppercase;
  }
  .main-nav a { color: var(--white); text-decoration: none; }
  .main-nav .nav-signin {
    background: var(--nav-pill); padding: 6px 14px; border-radius: 3px;
    box-shadow: 0 2px 5px rgba(0,0,0,.3); margin-left: -14px;
  }
  .hero-art {
    position: absolute; left: 170px; top: 125px; width: 290px; height: 348px;
    background: linear-gradient(160deg, var(--worker-a), var(--worker-b));
    border-radius: 6px; opacity: .85;
  }
  .signin-card {
    position: absolute; left: 451px; top: 184px; width: 299px; height: 300px;
    background: var(--white); border-radius: 3px;
    box-shadow: 0 6px 24px rgba(0,0,0,.3);
    padding: 0 17px;
  }
  .signin-title {
    text-align: center; color: var(--ink); font-size: 21px; font-weight: 700;
    padding: 30px 0 14px; border-bottom: 1px solid var(--rule);
  }
  .field {
    display: block; width: 266px; height: 46px; margin-top: 20px;
    border: 1px solid var(--field-border); border-radius: 3px;
    padding: 0 18px; font: 400 16px "Raleway", sans-serif; color: var(--muted);
    background: var(--white);
  }
  .field-email { border-color: transparent; box-shadow: 0 2px 8px rgba(0,0,0,.3); }
  .login-btn {
    display: block; width: 266px; height: 45px; margin-top: 19px;
    border: none; border-radius: 2px; background: var(--sky); color: var(--white);
    font: 500 19px "Raleway", sans-serif; box-shadow: 0 3px 8px rgba(0,0,0,.3);
  }
  .site-footer {
    position: absolute; left: 0; top: 585px; width: 1200px; height: 90px;
    background: var(--footer);
  }
  .copyright { position: absolute; left: 86px; top: 37px; font-size: 13px; }
  .social { position: absolute; left: 971px; top: 32px; display: flex; gap: 5px; }
  .social span { width: 25px; height: 25px; border-radius: 50%; }
</style>
</head>
<body>
  <header class="site-header">
    <div class="brand"><span class="brand-dot"></span>Yakhaul</div>
    <nav class="main-nav">
      <a href="#">Book</a>
      <a href="#">How it works</a>
      <a href="#">Become a driver</a>
      <a href="#" class="nav-signin">Sign in</a>
    </nav>
  </header>

  <div class="hero-art" role="img" aria-label="Illustration of a worker in orange overalls wheeling a recycling bin"></div>

  <form class="signin-card">
    <h1 class="signin-title">Please sign in</h1>
    <input class="field field-email" type="email" placeholder="Email address">
    <input class="field" type="password" placeholder="Password">
    <button class="login-btn" type="button">Login</button>
  </form>

  <footer class="site-footer">
    <p class="copyright">2017 © Yakhaul. All rights reserved.</p>
    <div class="social" aria-label="Social links">
      <span style="background:var(--soc-1)"></span>
      <span style="background:var(--soc-2)"></span>
      <span style="background:var(--soc-3)"></span>
      <span style="background:var(--soc-4)"></span>
      <span style="background:var(--soc-5)"></span>
    </div>
  </footer>
</body>
</html>
```